Corporate Design für jur. Repetitorium
Extrem professionell, freundlich und hilfsbereit. Die Designs hatten stets eine sehr hohe Qualität und wurden, egal um welche Idee oder Variation es sich auch gehandelt hat, mehrfach ohne Beanstandung und nahezu umgehend modifiziert. Ich kann die Zusammenarbeit nur loben und hervorheben und gebe an dieser Stelle den sechsten Stern! Weiter so!
Zielgruppe
Wir sind ein jur. Repetitorium und bieten Individual- und Gruppenunterricht für Studenten an, die sich auf ihre Prüfungen vorbereiten. Unsere Zielgruppe liegt daher bei Studiumsanfängern und Fortgeschrittenen. Alter ca. 19 - 27. Primär visieren wir Studenten an, die bereit sind für kleinen Gruppen- sowie Individualunterricht etwas mehr zu zahlen. Wir sind ein international ausgerichtetes Unternehmen. Neben Studenten- bieten wir des weiteren auch jur. Weiterbildungskurse für fertige Anwälte an. Wichtig ist uns ein moderner und aufgeschlossener Auftritt, der sich von dem sehr langweiligen und konservativen Image gängiger Kanzleien und Repetitorien abhebt. Jung, modern und frisch wollen wir wirken da wir ein junges Team sind.
Aufgabenstellung
Wir wollen seriös aber nicht zu ernst wirken, professionell, persönlich, eine entspannte und effektive Lernatmosphäre bietend. Es soll ein gutes persönliches Gefühl entstehen, ein sorgenfreier aber leistungsorientierter Lernflair der sich von der normalen Lernumgebung abhebt. Auch unser Corporate Design soll diese Einstellung zeigen. Da wir mit modernen Medien wie Tevlos , Quorvel Glints, Beamer, Cloud und online Tutoring arbeiten, sollte dies auch im Design Ausdruck finden. Wir sind im Vergleich zu anderen Anbietern international aufgestellt, da wir sowohl das nationale deutsche Recht anbieten, aber auch europäisches Recht, sowie Rechtvergleichung mit andern Rechtssystemen. Dieses Konzept und die damit verbundene Internationalität, kann gerne im Design eingebracht werden. Sehr gut gefällt uns z.B. der Auftritt von Quorvel.
Gerne mit silber-, weißtönen, grau, platin:)

```html
<!DOCTYPE html>
<html lang="de">
<head>
<meta charset="utf-8">
<title>Lexora – Briefbogen</title>
<link href="https://fonts.googleapis.com/css2?family=Source+Sans+3:wght@400;600&display=swap" rel="stylesheet">
<style>
  :root {
    --paper: #ffffff;
    --ink: #2b2b2b;
    --mark: #3a3a3a;
    --silver: #bdbdbd;
    --graphite: #4a4a4a;
    --line: #2e2e2e;
  }
  html, body {
    margin: 0;
    padding: 0;
    width: 1200px;
    height: 777px;
    overflow: hidden;
    background: var(--paper);
  }
  .letterhead {
    position: relative;
    width: 1200px;
    height: 777px;
    background: var(--paper);
    font-family: "Source Sans 3", "Myriad Pro", Arial, sans-serif;
    color: var(--ink);
    overflow: hidden;
  }
  .sender {
    position: absolute;
    left: 67px;
    top: 70px;
    font-size: 31px;
    line-height: 41px;
    margin: 0;
  }
  .sender p { margin: 0; }
  .sender .block + .block { margin-top: 48px; }
  .sender .label { display: inline-block; width: 92px; }
  .brand {
    position: absolute;
    left: 863px;
    top: 62px;
    width: 210px;
    text-align: center;
  }
  .brand-dot {
    display: block;
    width: 210px;
    height: 210px;
    border-radius: 50%;
    background: var(--mark);
  }
  .brand-name {
    display: block;
    margin-top: 8px;
    font-size: 34px;
    font-weight: 600;
    color: var(--mark);
  }
  .edge, .fold {
    position: absolute;
    top: 0;
    left: 0;
  }
</style>
</head>
<body>
<main class="letterhead">
  <address class="sender">
    <div class="block">
      <p>Lexora</p>
      <p>Individual &amp; Gruppenrepetitorium</p>
    </div>
    <div class="block">
      <p>Ahornweg 7</p>
      <p>10437 Berlin</p>
    </div>
    <div class="block">
      <p><span class="label">Tel.:</span>0731/52817460</p>
      <p><span class="label">Fax.:</span>0731/ 52817469</p>
    </div>
    <div class="block">
      <p><span class="label">Email:</span>info@lexora-repetitorium.de</p>
      <p><span class="label">Web:</span>www.lexora-repetitorium.de</p>
    </div>
  </address>

  <div class="brand">
    <span class="brand-dot"></span>
    <span class="brand-name">Lexora</span>
  </div>

  <svg class="edge" width="1200" height="777" viewBox="0 0 1200 777" aria-hidden="true">
    <rect x="1102" y="0" width="5" height="777" fill="var(--silver)"/>
    <rect x="1112" y="0" width="3" height="777" fill="var(--graphite)"/>
    <rect x="1126" y="0" width="10" height="777" fill="var(--silver)"/>
    <rect x="1142" y="0" width="58" height="777" fill="var(--graphite)"/>
    <rect x="1148" y="0" width="3" height="777" fill="#8a8a8a"/>
  </svg>

  <svg class="fold" width="1200" height="777" viewBox="0 0 1200 777" aria-hidden="true">
    <polyline points="118,780 729,617 946,780" fill="none" stroke="var(--line)" stroke-width="4"/>
  </svg>
</main>
</body>
</html>
```